FunBrixo Business Card

We need a business card design for our company. We sell construction-themed amusement rides for kids.

Contact Information for Business Card

Contact info on business card should include:
Carl Dunning
Co-Founder & COO
(833) 571-FUNBRIX
Carl@funbrixo-demo.com
www.funbrixo-demo.com

```html
<!DOCTYPE html>
<html lang="en">
<head>
<meta charset="utf-8">
<title>FunBrixo Business Card</title>
<link rel="stylesheet" href="https://fonts.googleapis.com/css2?family=Arimo:wght@400;700&display=swap">
<style>
  :root {
    --page-bg: #1c1c1e;
    --card-white: #ffffff;
    --brand-orange: #e8502a;
    --ink: #1a1a1a;
    --logo-dark: #111111;
    --sky-blue: #3f86c4;
    --sky-light: #a9c9df;
    --sunset-peach: #f2b48a;
    --machine-orange: #e98a2a;
    --art-yellow: #f5c84a;
    --art-skin: #f3d2b6;
    --art-blue: #3e6fb0;
  }
  * { box-sizing: border-box; margin: 0; padding: 0; }
  html, body {
    width: 1200px;
    height: 900px;
    overflow: hidden;
    background: var(--page-bg);
    font-family: "Arimo", Arial, sans-serif;
  }
  .sheet {
    position: relative;
    width: 1200px;
    height: 900px;
    display: flex;
    flex-direction: column;
    align-items: center;
    justify-content: center;
    gap: 48px;
  }
  .card {
    position: relative;
    width: 640px;
    height: 366px;
    overflow: hidden;
    border-radius: 2px;
  }

  /* Front side */
  .card-front__photo {
    position: absolute;
    inset: 0;
    background: linear-gradient(180deg,
      var(--sky-blue) 0%,
      var(--sky-light) 30%,
      var(--sunset-peach) 52%,
      var(--machine-orange) 78%,
      #c9702a 100%);
  }
  .card-front__brand {
    position: absolute;
    top: 52px;
    left: 340px;
    display: flex;
    align-items: center;
    gap: 12px;
    font-weight: 700;
    font-size: 52px;
    color: var(--logo-dark);
    letter-spacing: -1px;
  }
  .brand-mark {
    width: 26px;
    height: 26px;
    border-radius: 50%;
    background: currentColor;
  }

  /* Back side */
  .card-back { background: var(--card-white); }
  .card-back__brand {
    position: absolute;
    top: 96px;
    left: 44px;
    font-weight: 700;
    font-size: 54px;
    color: var(--brand-orange);
    letter-spacing: -1px;
  }
  .card-back__art {
    position: absolute;
    top: 40px;
    right: 28px;
    width: 300px;
    height: 230px;
    border-radius: 8px;
    background: radial-gradient(ellipse at 35% 30%, var(--art-yellow) 0%, transparent 45%),
                radial-gradient(ellipse at 70% 22%, var(--art-yellow) 0%, transparent 40%),
                linear-gradient(180deg, var(--art-skin) 0%, #e9e2dc 45%, var(--art-blue) 100%);
    opacity: 0.9;
  }
  .contact {
    position: absolute;
    left: 44px;
    top: 196px;
  }
  .contact__name {
    font-weight: 700;
    font-size: 26px;
    color: var(--brand-orange);
    letter-spacing: 0.5px;
  }
  .contact__role {
    font-size: 19px;
    color: var(--ink);
    margin-top: 4px;
  }
  .contact__list {
    list-style: none;
    margin-top: 12px;
  }
  .contact__item {
    display: flex;
    align-items: center;
    gap: 12px;
    font-size: 19px;
    color: var(--ink);
    line-height: 1.45;
  }
  .contact__icon {
    width: 20px;
    height: 20px;
    flex: none;
  }
</style>
</head>
<body>
<main class="sheet">

  <section class="card card-front">
    <div class="card-front__photo" role="img" aria-label="Photo of orange construction-themed kids rides at a seaside amusement park under a sunset sky"></div>
    <div class="card-front__brand"><span class="brand-mark"></span>FunBrixo</div>
  </section>

  <section class="card card-back">
    <div class="card-back__brand">FunBrixo</div>
    <div class="card-back__art" role="img" aria-label="Cartoon illustration of two construction workers in yellow hard hats shaking hands"></div>

    <div class="contact">
      <p class="contact__name">CARL DUNNING</p>
      <p class="contact__role">Co-Founder &amp; COO</p>
      <ul class="contact__list">
        <li class="contact__item">
          <svg class="contact__icon" viewBox="0 0 20 20" aria-hidden="true">
            <rect x="1" y="1" width="18" height="18" rx="3" fill="none" stroke="var(--brand-orange)" stroke-width="1.6"/>
            <path d="M6 5.5c0 5 3.5 9 8.5 9l.8-2.2-2.6-1.2-1.2 1.2c-1.6-.8-2.8-2-3.6-3.6l1.2-1.2L7.9 4.8z" fill="var(--brand-orange)"/>
          </svg>
          (833) 571-FUNBRIX
        </li>
        <li class="contact__item">
          <svg class="contact__icon" viewBox="0 0 20 20" aria-hidden="true">
            <rect x="1" y="4" width="18" height="12" rx="1" fill="var(--brand-orange)"/>
            <path d="M1.5 4.8 10 11l8.5-6.2" fill="none" stroke="#fff" stroke-width="1.4"/>
          </svg>
          Carl@funbrixo-demo.com
        </li>
        <li class="contact__item">
          <svg class="contact__icon" viewBox="0 0 20 20" aria-hidden="true">
            <circle cx="10" cy="10" r="9" fill="var(--brand-orange)"/>
            <g fill="none" stroke="#fff" stroke-width="1.1">
              <ellipse cx="10" cy="10" rx="4" ry="9"/>
              <path d="M1 10h18M2.5 5.5h15M2.5 14.5h15M10 1v18"/>
            </g>
          </svg>
          www.funbrixo-demo.com
        </li>
      </ul>
    </div>
  </section>

</main>
</body>
</html>
```